sydney wedding photography business needs a business card design

we need a business card design for a sydney based wedding photography and videography business. our business name is :golden hour studio and film. our target clients are 24-35 yrs female. our style is candid, organic, natural, dynamic. we are a team of young photographers and videographers, and help brides to create memories that they will cherish for the rest of their lives. the logo will be provided. we want an elegant design that reflects our style, and also want to give a great impression to our clients that we are one of the best studios in sydney and our brand means quality and premium service.

Target Market(s)

bride to be, 24-35 years old, living in sydney and surrunding areas

Industry/Entity Type

Wedding Photography

Contact Information for Business Card

address: 57 tarrant street, glenmore nsw 2047
mobile: 0431872259
phone: (02) 9163 2408
info@tidewillowstudio.net.au
www.tidewillowstudio.net.au
facebook:tidewillowweddings
instagram:tidewillowweddings

Font styles to use
Serif
Sans Serif

Requirements
Nice to have
• maybe add my slogan"memories beyond eternity" if the layout looks good
Should not have
• no black color, not good idea for wedding biz card

```html
<!DOCTYPE html>
<html lang="en">
<head>
<meta charset="utf-8">
<title>Golden Hour Studio and Film — Business Card</title>
<link rel="stylesheet" href="https://fonts.googleapis.com/css2?family=Roboto:wght@300;400;500&display=swap">
<style>
  :root {
    --backdrop: #4a4a4c;
    --card: #f6f0e4;
    --card-edge: #e9dfcc;
    --gold: #b8861b;
    --gold-soft: #d4ab4e;
    --ink: #3b3027;
    --ink-soft: #5a4d41;
  }
  * { margin: 0; padding: 0; box-sizing: border-box; }
  html, body { width: 1200px; height: 950px; overflow: hidden; }
  body {
    background: var(--backdrop);
    font-family: "Roboto", Arial, sans-serif;
    position: relative;
  }
  .card {
    position: absolute;
    width: 580px;
    height: 332px;
    background: linear-gradient(135deg, var(--card) 0%, var(--card) 60%, var(--card-edge) 100%);
    border-radius: 4px;
    box-shadow: 0 14px 30px rgba(0,0,0,0.45);
    overflow: hidden;
  }
  .card--front { left: 70px; top: 110px; }
  .card--back { left: 550px; top: 508px; }

  /* front */
  .front-brand {
    position: absolute;
    top: 78px; left: 0; right: 0;
    display: flex; align-items: center; justify-content: center; gap: 14px;
    color: var(--gold);
    font-size: 26px; font-weight: 400; letter-spacing: 0.5px;
  }
  .brand-dot {
    width: 18px; height: 18px; border-radius: 50%;
    background: var(--gold);
  }
  .front-rule {
    position: absolute; top: 206px; left: 40px; right: 40px; height: 1px;
    background: linear-gradient(90deg, transparent, var(--gold) 30%, var(--gold) 70%, transparent);
  }
  .front-rule__dot {
    position: absolute; left: 50%; top: -6px; margin-left: -6px;
    width: 12px; height: 12px; border-radius: 50%;
    background: var(--gold); border: 2px solid var(--card);
  }
  .social-handle {
    position: absolute; top: 222px; left: 0; right: 0;
    text-align: center; color: var(--ink);
    font-size: 15px; font-weight: 300; letter-spacing: 0.3px;
  }

  /* back */
  .name-block {
    position: absolute; left: 24px; top: 44px;
    border-left: 8px solid var(--gold);
    padding-left: 16px;
  }
  .person-name { color: var(--gold); font-size: 19px; font-weight: 500; }
  .person-title { color: var(--ink); font-size: 14px; font-weight: 400; margin-top: 3px; }
  .address {
    position: absolute; left: 48px; top: 118px;
    color: var(--ink-soft); font-size: 13px; font-weight: 400; line-height: 1.4;
  }
  .contact-list {
    position: absolute; left: 48px; top: 162px;
    list-style: none;
    color: var(--ink-soft); font-size: 13px; font-weight: 400;
  }
  .contact-list li { display: flex; align-items: center; gap: 9px; line-height: 21px; }
  .contact-list svg { width: 12px; height: 12px; fill: var(--gold); flex: none; }
  .back-brand {
    position: absolute; left: 48px; bottom: 32px;
    color: var(--gold); font-size: 22px; font-weight: 400; letter-spacing: 0.3px;
  }
</style>
</head>
<body>

<section class="card card--front" aria-label="Business card front">
  <div class="front-brand"><span class="brand-dot"></span>golden hour studio and film</div>
  <div class="front-rule"><span class="front-rule__dot"></span></div>
  <p class="social-handle">tidewillowweddings</p>
</section>

<section class="card card--back" aria-label="Business card back">
  <div class="name-block">
    <p class="person-name">Mara Linden</p>
    <p class="person-title">President</p>
  </div>
  <p class="address">57 tarrant street<br>glenmore nsw 2047</p>
  <ul class="contact-list">
    <li><svg viewBox="0 0 12 12" aria-hidden="true"><path d="M2 1h2.5l1 3-1.5 1c.7 1.4 1.6 2.3 3 3l1-1.5 3 1V11c-5 0-9-4-9-9z"/></svg>(02) 9163 2408</li>
    <li><svg viewBox="0 0 12 12" aria-hidden="true"><path d="M3 0h6v12H3zM4 1.5v8h4v-8z"/></svg>0431 872 259</li>
    <li><svg viewBox="0 0 12 12" aria-hidden="true"><path d="M0 2h12v8H0zM1 3l5 3.5L11 3z"/></svg>info@tidewillowstudio.net.au</li>
    <li><svg viewBox="0 0 12 12" aria-hidden="true"><circle cx="6" cy="6" r="5.5"/></svg>tidewillowstudio.net.au</li>
  </ul>
  <p class="back-brand">golden hour studio and film</p>
</section>

</body>
</html>
```